Non fiction leadership Book Cover design needed for “Stay Bold: Build On Lasting Discipline”

I need a front cover design for a new book 6 X 9 traditional non-fiction book.

Title: "Stay BOLD - Build On Lasting Discipline"

The subtitle is not finalized- so use 2 lines of smaller dummy text

My brand guide is attached (please use the tan color sparingly)

I'd like to see BOLD look like it is in motion and "flying" across the page

Need CREATIVE designs and options

Do not want my picture on the front cover - I do want it on the back cover.

On the front cover I’d like to see creative use of font to create movement on “BOLD”

Target Market(s)

Business leaders

Industry/Entity Type

Aviation

Font styles to use
Other font styles liked:
• See style guide- can add additional font (modern script or san serif)

Colors
0054AA
0677BA
7BADD7
CADEEF
E8F1F8
EB3D1F
EC4F4E
F09395
F8D3D4
FCEDEE

Requirements
Must have
• Creative font use, using perspective to create movement/motion on BOLD
Should not have
• My picture on the front cover- my picture should be on the back cover

```html
<!DOCTYPE html>
<html lang="en">
<head>
<meta charset="utf-8">
<title>Stay Bold: Build On Lasting Discipline — Front Cover</title>
<link rel="stylesheet" href="https://fonts.googleapis.com/css2?family=Bebas+Neue&family=Montserrat:wght@400;600&display=swap">
<style>
  :root {
    --backdrop: #c6c6c6;
    --cover-ink: #03020f;
    --title-red: #ee1c25;
    --title-cream: #fbf3ee;
    --text-white: #ffffff;
  }
  * { margin: 0; padding: 0; box-sizing: border-box; }
  html, body {
    width: 1200px;
    height: 1200px;
    overflow: hidden;
    background: var(--backdrop);
  }
  .cover {
    position: absolute;
    left: 200px;
    top: 0;
    width: 800px;
    height: 1200px;
    background: var(--cover-ink);
    font-family: "Montserrat", sans-serif;
    color: var(--text-white);
  }
  .cover__teaser {
    position: absolute;
    top: 46px;
    left: 0;
    width: 100%;
    text-align: center;
    font-size: 17px;
    line-height: 28px;
    letter-spacing: 0.04em;
  }
  .cover__title-art {
    position: absolute;
    left: 0;
    top: 0;
    width: 800px;
    height: 1200px;
  }
  .title-lead {
    font-family: "Bebas Neue", sans-serif;
    font-size: 150px;
    fill: var(--title-cream);
  }
  .title-main {
    font-family: "Bebas Neue", sans-serif;
    font-size: 786px;
    fill: var(--title-red);
  }
  .title-main-motion {
    transform: skewX(-8deg);
    transform-origin: 400px 896px;
  }
  .motion-cut { fill: var(--cover-ink); }
  .cover__subtitle {
    position: absolute;
    top: 914px;
    left: 80px;
    width: 640px;
    font-size: 28px;
    letter-spacing: 0.12em;
    white-space: nowrap;
    text-align: center;
  }
  .cover__author {
    position: absolute;
    top: 1078px;
    left: 0;
    width: 100%;
    text-align: center;
    font-size: 40px;
    font-weight: 600;
    color: var(--title-red);
  }
</style>
</head>
<body>
  <main class="cover">
    <p class="cover__teaser">Lorem ipsum dolor sit amet, consectetuer adipiscing<br>sed diam nonummy nibh euismod tincidunt</p>

    <svg class="cover__title-art" viewBox="0 0 800 1200" xmlns="http://www.w3.org/2000/svg" aria-labelledby="cover-title">
      <title id="cover-title">Stay BOLD</title>
      <text class="title-lead" x="398" y="316" text-anchor="middle">STAY</text>
      <g class="title-main-motion">
        <text class="title-main" x="110" y="896" textLength="580" lengthAdjust="spacingAndGlyphs">BOLD</text>
        <rect class="motion-cut" x="540" y="330" width="16" height="580"
              role="img" aria-label="Dark silhouette of a helicopter flying upward through the title letters"/>
      </g>
    </svg>

    <p class="cover__subtitle">BUILD ON LASTING DISCIPLINE</p>
    <p class="cover__author">Margaret Ellison</p>
  </main>
</body>
</html>
```